I would like a business card to match my truck wrap and logo. I would like the font to match my existing business card please.

Industry/Entity Type

Painter

Contact Information for Business Card

Rodrigo Fenwar 801-437-2190 Fenwarcoatings.utah@brelmox.com
SERVICES - Custom Paint & Stain, Interior & Exterior, Epoxy Coatings / Garage Floors, Cabinet Refinishing, Log Staining and Refinishing.

Requirements
Nice to have
• I would like to have the white and grey line like the bottom of my vehicle wrap, Light Grey to match my truck also.

```html
<!DOCTYPE html>
<html lang="en">
<head>
<meta charset="utf-8">
<title>Fenwar Painting — Business Card</title>
<link href="https://fonts.googleapis.com/css2?family=Arimo:wght@400;700&family=Michroma&display=swap" rel="stylesheet">
<style>
  :root {
    --stage: #0e0e0f;
    --card: #252628;
    --card-edge: #1c1d1f;
    --blue: #0aa3f0;
    --blue-deep: #0a6fb8;
    --text-light: #d9dadc;
    --rule: #55575b;
  }
  * { box-sizing: border-box; margin: 0; padding: 0; }
  html, body { width: 1200px; height: 820px; overflow: hidden; background: var(--stage); }
  .stage {
    width: 1200px; height: 820px;
    display: flex; align-items: center; justify-content: center; gap: 40px;
  }
  .card {
    position: relative;
    width: 540px; height: 309px;
    background: linear-gradient(160deg, #2a2b2e 0%, var(--card) 60%, var(--card-edge) 100%);
    border-left: 2px solid var(--blue-deep);
    border-bottom: 2px solid var(--blue-deep);
    box-shadow: 0 18px 40px rgba(0,0,0,.6);
    overflow: hidden;
  }
  .wordmark { position: absolute; display: flex; align-items: center; gap: 12px; }
  .wordmark__square { width: 30px; height: 30px; background: var(--blue); border-radius: 4px; }
  .wordmark__name {
    font-family: "Michroma", sans-serif;
    color: var(--blue);
    line-height: 1.15;
    letter-spacing: .06em;
  }
  .front .wordmark { top: 78px; left: 190px; }
  .front .wordmark__name { font-size: 24px; }
  .front .divider {
    position: absolute; left: 250px; right: 20px; top: 200px;
    height: 1px; background: var(--rule);
  }
  .contact-name {
    position: absolute; left: 36px; top: 188px;
    font-family: "Michroma", sans-serif; font-size: 17px;
    color: var(--blue); letter-spacing: .02em;
  }
  .contact-list {
    position: absolute; left: 36px; top: 230px;
    list-style: none;
    font-family: "Arimo", sans-serif; font-size: 14px; color: var(--text-light);
  }
  .contact-list li { display: flex; align-items: center; gap: 9px; margin-bottom: 7px; }
  .contact-list svg { width: 15px; height: 15px; fill: var(--blue); flex: none; }
  .back .wordmark { top: 38px; right: 42px; }
  .back .wordmark__name { font-size: 22px; text-align: right; }
  .services {
    position: absolute; top: 122px; right: 34px; width: 270px;
    list-style: none;
    font-family: "Arimo", sans-serif; font-size: 13.5px; color: var(--text-light);
  }
  .services li { display: flex; align-items: center; gap: 8px; margin-bottom: 11px; }
  .services li::before {
    content: ""; width: 7px; height: 7px; border-radius: 50%;
    background: var(--blue); flex: none;
  }
</style>
</head>
<body>
<main class="stage">
  <section class="card front" aria-label="Card front">
    <div class="wordmark">
      <span class="wordmark__square"></span>
      <span class="wordmark__name">FENWAR<br>PAINTING</span>
    </div>
    <div class="divider"></div>
    <h1 class="contact-name">RODRIGO FENWAR</h1>
    <ul class="contact-list">
      <li>
        <svg viewBox="0 0 24 24" aria-hidden="true"><path d="M6.6 10.8a15.1 15.1 0 0 0 6.6 6.6l2.2-2.2c.3-.3.7-.4 1-.2 1.1.4 2.3.6 3.6.6.6 0 1 .4 1 1V20c0 .6-.4 1-1 1A17 17 0 0 1 3 4c0-.6.4-1 1-1h3.5c.6 0 1 .4 1 1 0 1.3.2 2.5.6 3.6.1.3 0 .7-.2 1z"/></svg>
        <span>801-437-2190</span>
      </li>
      <li>
        <svg viewBox="0 0 24 24" aria-hidden="true"><path d="M2 5h20v14H2zm2 2v.5l8 5 8-5V7zm0 2.8V17h16V9.8l-8 5z"/></svg>
        <span>Fenwarcoatings.utah@brelmox.com</span>
      </li>
    </ul>
  </section>

  <section class="card back" aria-label="Card back">
    <div class="wordmark">
      <span class="wordmark__name">FENWAR<br>PAINTING</span>
    </div>
    <ul class="services">
      <li>Custom Paint &amp; Stain</li>
      <li>Interior &amp; Exterior</li>
      <li>Epoxy Coatings / Garage Floors</li>
      <li>Cabinet Refinishing</li>
      <li>Log Staining and Refinishing.</li>
    </ul>
  </section>
</main>
</body>
</html>
```